4th Generation Family Business Needs a New Card Design!

We are a family owned 4th Generation company. We are based in the Sydney, Australia area and we are desperately in need of a more modern and classy card. We are monumental masons who design, supply & erect lasting memorials throughout cemeteries in Sydney. Our customers are normally in a period of grieving. I have attached logo files that will need to be implemented on the card. Company was established 1935. Australian Owned and Operated. Card needs to be designed to PIXO.com specification.

Target Market(s)

Our target market is based upon people that a grieving for family members that have passed away. We also deal with alot of companies that own and operate cemeteries.

Industry/Entity Type

Business

Contact Information for Business Card

Simon Harcourt, Operations Manager, 0417293086, simon@harcourtmemorials.com.au
Lewis Harcourt, Director, 0491630572, lewis@harcourtmemorials.com.au
Phone # 02 9561 3048
Website: www.harcourtmemorials.com.au
Address: Suite 17, 8 Palfrey Lane, West Carlow, Sydney NSW 2156

Font styles to use
Serif
Decorative
Script

Requirements
Must have
• Would like to see the logo nicely implemented with a modern design. Embossed lettering would be a nice additive.

```html
<!DOCTYPE html>
<html lang="en">
<head>
<meta charset="utf-8">
<title>Harcourt Memorials – Business Card</title>
<link href="https://fonts.googleapis.com/css2?family=Cinzel:wght@400;600&family=Libre+Baskerville:wght@400;700&display=swap" rel="stylesheet">
<style>
  :root {
    --stage: #2b2b2b;
    --card: #0c0c0c;
    --gold: #f0c12a;
    --white: #ffffff;
    --ink: #111111;
  }
  html, body {
    margin: 0;
    padding: 0;
    width: 1189px;
    height: 1200px;
    overflow: hidden;
    background: var(--stage);
  }
  .stage {
    position: relative;
    width: 1189px;
    height: 1200px;
  }
  .card {
    position: absolute;
    left: 173px;
    width: 854px;
    height: 487px;
    background: var(--card);
    border-radius: 16px;
    overflow: hidden;
    box-shadow: 0 6px 18px rgba(0,0,0,0.55);
  }
  .card--front { top: 68px; }
  .card--back { top: 627px; }

  .card__band {
    position: absolute;
    left: 0;
    bottom: 0;
    width: 854px;
    height: 62px;
  }
  .card__web {
    position: absolute;
    left: 0;
    right: 0;
    top: 447px;
    text-align: center;
    font-family: "Libre Baskerville", serif;
    font-weight: 700;
    font-size: 19px;
    color: var(--ink);
  }

  /* brand block: plain square + name */
  .brand {
    position: absolute;
    display: flex;
    flex-direction: column;
    align-items: center;
  }
  .card--front .brand { left: 227px; width: 400px; top: 108px; }
  .card--back .brand { left: 459px; width: 400px; top: 62px; }

  .brand__square {
    box-sizing: border-box;
    border: 5px solid var(--white);
  }
  .card--front .brand__square { width: 134px; height: 134px; }
  .card--back .brand__square { width: 128px; height: 128px; }

  .brand__name {
    font-family: "Cinzel", serif;
    font-weight: 400;
    color: var(--white);
    text-align: center;
    text-transform: uppercase;
    line-height: 1;
  }
  .card--front .brand__name { font-size: 58px; margin-top: 14px; }
  .card--back .brand__name { font-size: 56px; margin-top: 22px; }
  .brand__small {
    display: block;
    font-size: 0.5em;
    letter-spacing: 2px;
    margin-top: 4px;
  }

  .person {
    position: absolute;
    left: 50px;
    top: 74px;
  }
  .person__name {
    font-family: "Cinzel", serif;
    font-weight: 600;
    font-size: 31px;
    color: var(--white);
    line-height: 1;
    margin: 0;
  }
  .person__role {
    font-family: "Libre Baskerville", serif;
    font-size: 21px;
    color: var(--gold);
    line-height: 1;
    margin: 0;
  }

  .address {
    position: absolute;
    left: 50px;
    top: 225px;
    font-family: "Libre Baskerville", serif;
    font-style: normal;
    font-size: 23px;
    line-height: 31px;
    color: var(--white);
  }

  .contacts {
    position: absolute;
    left: 50px;
    top: 305px;
    margin: 0;
    padding: 0;
    list-style: none;
    font-family: "Libre Baskerville", serif;
    font-size: 22px;
    color: var(--white);
  }
  .contacts__item {
    display: flex;
    align-items: center;
    height: 28px;
  }
  .contacts__icon {
    width: 24px;
    height: 20px;
    margin-right: 14px;
    fill: var(--gold);
  }
</style>
</head>
<body>
<main class="stage">

  <section class="card card--front" aria-label="Card front">
    <div class="brand">
      <div class="brand__square" aria-hidden="true"></div>
      <div class="brand__name">Harcourt<span class="brand__small">Memorials</span></div>
    </div>
    <svg class="card__band" viewBox="0 0 854 62" aria-hidden="true">
      <path d="M0 57 Q427 -40 854 57 L854 62 L0 62 Z" fill="var(--gold)"/>
    </svg>
    <div class="card__web">www.harcourtmemorials.com.au</div>
  </section>

  <section class="card card--back" aria-label="Card back">
    <div class="person">
      <h1 class="person__name">Simon Harcourt</h1>
      <p class="person__role">Operations Manager</p>
    </div>

    <address class="address">
      Suite 17, 8 Palfrey Lane,<br>
      West Carlow, Sydney NSW 2156
    </address>

    <ul class="contacts">
      <li class="contacts__item">
        <svg class="contacts__icon" viewBox="0 0 24 20" aria-hidden="true">
          <rect x="6" y="0" width="12" height="20" rx="2"/>
          <rect x="8" y="3" width="8" height="6" fill="var(--card)"/>
        </svg>
        0417293086
      </li>
      <li class="contacts__item">
        <svg class="contacts__icon" viewBox="0 0 24 20" aria-hidden="true">
          <path d="M1 6 Q12 -2 23 6 L20 9 L16 6 L8 6 L4 9 Z"/>
          <rect x="4" y="10" width="16" height="10" rx="2"/>
        </svg>
        02 9561 3048
      </li>
      <li class="contacts__item">
        <svg class="contacts__icon" viewBox="0 0 24 20" aria-hidden="true">
          <rect x="1" y="3" width="22" height="15"/>
          <path d="M1 3 L12 12 L23 3 M1 18 L9 10 M23 18 L15 10" stroke="var(--card)" stroke-width="1.5" fill="none"/>
        </svg>
        simon@harcourtmemorials.com.au
      </li>
    </ul>

    <div class="brand">
      <div class="brand__square" aria-hidden="true"></div>
      <div class="brand__name">Harcourt<span class="brand__small">Memorials</span></div>
    </div>

    <svg class="card__band" viewBox="0 0 854 62" aria-hidden="true">
      <path d="M0 57 Q427 -40 854 57 L854 62 L0 62 Z" fill="var(--gold)"/>
    </svg>
    <div class="card__web">www.harcourtmemorials.com.au</div>
  </section>

</main>
</body>
</html>
```